NZ First of it's kind solutions directory and marketplace for busy Mums needs a business card design

We need a business card design for our new nationwide business in NZ (long term plans to go global). We provide solutions to the everyday challenges that busy Mums face by connecting them with quality communities and suppliers of carefully selected, relevant products and services. We sell direct via our online marketplace. The final design should communicate our values of inclusivity, quality and smart solutions. Colours should incorporate our logo colour palette of #477077 and #6ba8b2. Our website is at https://www.brightnestmums.example

Target Market(s)

busy Mums, Age 28 – 50, female, income over $100K, location main centres NZ primarily but NZ wide. Is likely juggling work or career with a young family. Probably had hobbies which have fallen by the wayside.
-Wants to succeed in her chosen career without compromising on family life
-to successfully juggle her career without feeling like she is compromising her children
- Is time poor, something always has to give and it’s generally her health (she’ll stay up late, get stressed)
- probably ex corporate or professional career. Has discretional income

Industry/Entity Type

Business

Contact Information for Business Card

Lena Forbisher, Founder, BrightNestMums.example (Strapline Tap; Gather; Sorted), 47 Kowhai Terrace, Ellerslie, Auckland 1051, New Zealand. Mob: 021 483 517 Ph: +64 (0)9 571 4860

Font styles to use
Other font styles liked:
• Raleway, and/or Architects Daughter

Colors
00a990
33b8a4
86cfc6
cfeae6

Requirements
Must have
• the above details, streamline. the logo and colours associated with those logos
Should not have
• foil or metallic colours

```html
<!DOCTYPE html>
<html lang="en">
<head>
<meta charset="utf-8">
<title>BrightNestMums business card</title>
<link rel="stylesheet" href="https://fonts.googleapis.com/css2?family=Work+Sans:wght@400;600;700&display=swap">
<style>
  :root {
    --teal-deep: #477077;
    --teal-light: #6ba8b2;
    --card-white: #ffffff;
    --backdrop: #3b3631;
    --ink-soft: #55797f;
  }
  * { margin: 0; padding: 0; box-sizing: border-box; }
  html, body {
    width: 1200px;
    height: 930px;
    overflow: hidden;
    background: var(--backdrop);
    font-family: "Work Sans", Arial, sans-serif;
  }
  .stage {
    width: 1200px;
    height: 930px;
    display: flex;
    flex-direction: column;
    align-items: center;
    justify-content: center;
    gap: 56px;
  }
  .card {
    width: 660px;
    height: 378px;
    border-radius: 22px;
    position: relative;
    overflow: hidden;
  }
  /* Front */
  .card--front {
    background: var(--teal-deep);
    display: flex;
    flex-direction: column;
    align-items: center;
    justify-content: center;
  }
  .brand {
    display: flex;
    align-items: center;
    gap: 18px;
    margin-top: -20px;
  }
  .brand__dot {
    width: 42px;
    height: 42px;
    border-radius: 50%;
    background: var(--card-white);
  }
  .brand__name {
    font-weight: 700;
    font-size: 54px;
    letter-spacing: -1.5px;
    color: var(--card-white);
  }
  .front__web {
    position: absolute;
    bottom: 44px;
    left: 0;
    right: 0;
    text-align: center;
    color: var(--card-white);
    font-size: 16px;
    letter-spacing: 1px;
  }
  /* Back */
  .card--back {
    background: var(--card-white);
    display: flex;
    align-items: center;
  }
  .back__brand {
    width: 290px;
    display: flex;
    flex-direction: column;
    align-items: center;
    gap: 16px;
  }
  .back__dot {
    width: 110px;
    height: 110px;
    border-radius: 50%;
    background: var(--teal-deep);
  }
  .back__name {
    font-weight: 700;
    font-size: 22px;
    letter-spacing: -0.5px;
    color: var(--teal-deep);
  }
  .divider {
    width: 2px;
    height: 170px;
    background: var(--teal-deep);
  }
  .contact {
    padding-left: 52px;
    color: var(--ink-soft);
    font-size: 15.5px;
    line-height: 1.45;
  }
  .contact__name {
    font-weight: 700;
    font-size: 30px;
    color: var(--teal-deep);
    letter-spacing: -0.5px;
    line-height: 1.05;
  }
  .contact__role {
    font-size: 16px;
    margin-bottom: 14px;
  }
  .contact__address { margin-bottom: 8px; }
  .contact__line {
    display: flex;
    align-items: center;
    gap: 8px;
  }
  .contact__line svg { width: 12px; height: 12px; flex: none; }
</style>
</head>
<body>
<main class="stage">
  <section class="card card--front" aria-label="Card front">
    <div class="brand">
      <span class="brand__dot"></span>
      <span class="brand__name">BrightNestMums</span>
    </div>
    <p class="front__web">www.brightnestmums.example</p>
  </section>

  <section class="card card--back" aria-label="Card back">
    <div class="back__brand">
      <span class="back__dot"></span>
      <span class="back__name">BrightNestMums</span>
    </div>
    <div class="divider"></div>
    <div class="contact">
      <p class="contact__name">Lena Forbisher</p>
      <p class="contact__role">Founder</p>
      <p class="contact__address">47 Kowhai Terrace, Ellerslie<br>Auckland 1051, New Zealand</p>
      <p class="contact__line">
        <svg viewBox="0 0 12 12" aria-hidden="true"><rect x="3" y="0.8" width="6" height="10.4" rx="1.2" fill="none" stroke="currentColor" stroke-width="1.2"/><line x1="5" y1="9.3" x2="7" y2="9.3" stroke="currentColor" stroke-width="1"/></svg>
        021 483 517
      </p>
      <p class="contact__line">
        <svg viewBox="0 0 12 12" aria-hidden="true"><path d="M3 1 L5 3.5 L4 5 Q5.5 7.5 7 8 L8.5 7 L11 9 L9.5 11 Q4 10.5 1 3 Z" fill="currentColor"/></svg>
        +64 (0)9 571 4860
      </p>
      <p class="contact__line">
        <svg viewBox="0 0 12 12" aria-hidden="true"><circle cx="6" cy="6" r="5" fill="none" stroke="currentColor" stroke-width="1.1"/><ellipse cx="6" cy="6" rx="2.2" ry="5" fill="none" stroke="currentColor" stroke-width="0.9"/><line x1="1" y1="6" x2="11" y2="6" stroke="currentColor" stroke-width="0.9"/></svg>
        www.brightnestmums.example
      </p>
    </div>
  </section>
</main>
</body>
</html>
```